Road Construction Company needs business cards

We would like a new business card designed for our business.

We're a road construction company based in Qld, Australia.

Can the business card please have the following information on it.

Name: Warren Halbeck
Position: General Manager
Phone: 0472 915 348
Email: Warren.halbeck@tovrin.com.au
Address: 87 Marrow Ave, Pendlebay, QLD, 4023
Website: www.tovrin.com.au

Visually we'd like the card to be professional and simple.

Attached is our logo.

Our website is www.tovrin.com.au

Target Market(s)

Men aged 25-60

Contact Information for Business Card

As listed in project description

Font styles to use
Serif

Requirements
Must have
• Large logo on back of card

```html
<!DOCTYPE html>
<html lang="en">
<head>
<meta charset="utf-8">
<title>Tovrin – Business Card</title>
<link href="https://fonts.googleapis.com/css2?family=Open+Sans:wght@400;700&display=swap" rel="stylesheet">
<style>
  :root {
    --bg: #2b2e33;
    --card: #222226;
    --edge: #3aa9de;
    --sky: #44ace0;
    --royal: #1559b8;
    --ink: #ffffff;
    --panel: rgba(96, 140, 150, 0.32);
  }
  * { margin: 0; padding: 0; box-sizing: border-box; }
  html, body { width: 1200px; height: 780px; overflow: hidden; }
  body {
    background: var(--bg);
    font-family: "Open Sans", Arial, sans-serif;
    color: var(--ink);
    position: relative;
  }
  .card {
    position: absolute;
    top: 232px;
    width: 520px;
    height: 316px;
    background: var(--card);
    border: 3px solid var(--edge);
    border-radius: 24px;
    overflow: hidden;
  }
  .card--front { left: 60px; }
  .card--back { left: 620px; }

  /* front */
  .front-logo {
    position: absolute;
    left: 30px;
    top: 30px;
    font-size: 44px;
    font-weight: 700;
    letter-spacing: 1px;
    color: var(--royal);
    line-height: 1;
  }
  .divider {
    position: absolute;
    left: 222px;
    top: 104px;
    width: 2px;
    height: 140px;
    background: var(--ink);
  }
  .details {
    position: absolute;
    left: 240px;
    top: 104px;
    width: 270px;
  }
  .details__name {
    font-size: 27px;
    font-weight: 700;
    color: var(--royal);
    line-height: 1.05;
  }
  .details__role {
    font-size: 13px;
    margin-top: 2px;
  }
  .details__address {
    font-size: 12.5px;
    line-height: 1.4;
    margin-top: 6px;
  }
  .details__contact {
    list-style: none;
    margin-top: 6px;
    font-size: 12.5px;
    line-height: 1.45;
  }
  .details__contact li { display: flex; align-items: center; gap: 6px; }
  .details__contact svg { width: 11px; height: 11px; flex: none; }
  .details__contact .no-icon { padding-left: 17px; }
  .bands {
    position: absolute;
    left: 0;
    bottom: 0;
    width: 514px;
    height: 40px;
  }

  /* back */
  .back-panel {
    position: absolute;
    inset: 0;
    width: 100%;
    height: 100%;
  }
  .back-logo {
    position: absolute;
    inset: 0;
    display: flex;
    align-items: center;
    justify-content: center;
    font-size: 96px;
    font-weight: 700;
    letter-spacing: 2px;
    color: var(--royal);
  }
</style>
</head>
<body>

  <section class="card card--front">
    <div class="front-logo">Tovrin</div>
    <div class="divider"></div>
    <div class="details">
      <div class="details__name">Warren Halbeck</div>
      <div class="details__role">General Manager</div>
      <div class="details__address">87 Marrow Ave,<br>Pendlebay, QLD, 4023</div>
      <ul class="details__contact">
        <li>
          <svg viewBox="0 0 12 12" aria-hidden="true"><path d="M3 1l2 2.5-1 1.2a6 6 0 0 0 3.3 3.3l1.2-1L11 9l-1.3 1.8C5.5 11 1 6.5 1.2 2.3z" fill="var(--sky)"/></svg>
          0472 915 348
        </li>
        <li>
          <svg viewBox="0 0 12 12" aria-hidden="true"><rect x="1" y="2.5" width="10" height="7" rx="1" fill="none" stroke="var(--sky)" stroke-width="1.3"/><path d="M1.5 3l4.5 3.5L10.5 3" fill="none" stroke="var(--sky)" stroke-width="1.2"/></svg>
          www.tovrin.com.au
        </li>
        <li>
          <svg viewBox="0 0 12 12" aria-hidden="true"><circle cx="6" cy="6" r="5" fill="none" stroke="var(--sky)" stroke-width="1.3"/><path d="M1 6h10M6 1c-2.5 3-2.5 7 0 10M6 1c2.5 3 2.5 7 0 10" fill="none" stroke="var(--sky)" stroke-width="1"/></svg>
          Warren.halbeck@tovrin.com.au
        </li>
      </ul>
    </div>
    <svg class="bands" viewBox="0 0 514 40" preserveAspectRatio="none" aria-hidden="true">
      <polygon points="0,12 170,12 196,40 0,40" fill="var(--sky)"/>
      <polygon points="206,14 514,14 514,40 218,40 206,28" fill="var(--royal)"/>
    </svg>
  </section>

  <section class="card card--back">
    <svg class="back-panel" viewBox="0 0 514 310" preserveAspectRatio="none" aria-hidden="true">
      <polygon points="0,0 26,0 74,310 0,310" fill="var(--panel)"/>
    </svg>
    <div class="back-logo">Tovrin</div>
  </section>

</body>
</html>
```